Lantern Petals Website v.1 - attract floral shop franchisees

I need a simple information website for my new business. We are a franchisor of flower shops. The overall purpose of the website is to promote the company and the service, especially to potential franchisees and retailers. Only about 4 pages are required including homepage, About, For Supermarkets, For Franchisees, and Contact. No special functions are required except the site will have two separate inquiry forms that must be filled out online and submitted via automated email. Similarly, an email form should be linked from the Contact page. I have a logo and business cards designed by ArtMingle, and I would like the site to have a consistent color scheme and style. The key to design will be to express the joy and love associated with flowers and floral bouquets.
IMPORTANT - I will be exporting the website design to Wordpress CMS in a site hosted by HostNimbus. For smooth integration into WordPress hosted by HostNimbus, the designer should build the site using a WordPress-friendly format. Ideally, they should use HTML, CSS, and PHP. Creating a custom theme or using a page builder that exports to WordPress-compatible files is best. This ensures the site can be easily imported and managed within WordPress.

Target Market(s)

Potential franchisees (existing florists or creative types who might like to own a floral business) and supermarkets who might want us to run their floral department

Industry/Entity Type

Floral retailing

Requirements
Must have
• A brand theme that is beautiful, consistent throughout and builds on the logo design
Nice to have
• Show gender and ethnic diversity in customers and florists. Pictures of happy florists (for franchisees) and pictures of amazing floral department displays (for supermarkets)

```html
<!DOCTYPE html>
<html lang="en">
<head>
<meta charset="utf-8">
<title>Lantern Petals – Franchisees</title>
<link rel="stylesheet" href="https://fonts.googleapis.com/css2?family=Libre+Baskerville:wght@400;700&family=Poppins:wght@400;500;600&display=swap">
<style>
:root{
  --orange:#f2ad2f;
  --orange-deep:#ef9c1c;
  --green:#0b8b3f;
  --green-dark:#107a3a;
  --ink:#1b1b1b;
  --grey-band:#e2e2e2;
  --paper:#ffffff;
  --link:#2b44c9;
}
*{margin:0;padding:0;box-sizing:border-box}
html,body{width:1200px;height:3106px;overflow:hidden;background:var(--paper)}
body{position:relative;font-family:"Poppins",sans-serif;color:var(--ink)}
.abs{position:absolute}
.serif{font-family:"Libre Baskerville",serif}

/* header */
.site-header{left:0;top:0;width:1200px;height:87px;background:#fff}
.brand-name{left:106px;top:30px;font-family:"Libre Baskerville",serif;font-size:20px;color:var(--orange-deep);display:flex;align-items:center;gap:8px}
.brand-dot{width:12px;height:12px;border-radius:50%;background:var(--green)}
.menu-toggle{left:1049px;top:30px;width:33px;height:22px;display:flex;flex-direction:column;justify-content:space-between}
.menu-toggle span{display:block;height:3px;background:#111}

/* hero */
.hero-photo{left:0;top:87px;width:1200px;height:433px;background:linear-gradient(90deg,#9fb55a 0%,#b9a276 28%,#d9b98c 45%,#d5b487 60%,#8d7896 78%,#d88fb6 100%)}
.hero-brand{left:0;width:1200px;top:343px;text-align:center;font-size:13px;font-weight:600;letter-spacing:.5px;color:#1a1a1a}
.hero-title{left:0;width:1234px;top:374px;text-align:center;font-size:40px;color:#111}

/* intro */
.hex-decor{left:90px;top:623px;width:163px;height:155px;background:var(--orange);opacity:.85;border-radius:24px}
.leaf-decor{left:1085px;top:627px;width:115px;height:247px;background:linear-gradient(160deg,rgba(14,140,62,.75),rgba(14,140,62,.2))}
.photo-ring{border-radius:50%;overflow:hidden}
.ring-orange{left:165px;top:627px;width:410px;height:410px;border:13px solid var(--orange)}
.ring-orange .fill{width:100%;height:100%;background:linear-gradient(150deg,#f4f2ef 0%,#e7dbd6 45%,#b79ac9 70%,#d6487c 100%)}
.intro-copy{left:625px;top:686px;width:455px;font-size:12.6px;line-height:19.5px}
.intro-copy p+p{margin-top:19px}

/* new florist */
.florist-band{left:0;top:1135px;width:1200px;height:444px;background:linear-gradient(90deg,#f3f3f3 0%,#f0eeed 42%,#c49f78 52%,#a48464 65%,#7a8aa0 80%,#d8d2cd 100%)}
.florist-photo-head{left:830px;top:1019px;width:150px;height:120px;background:linear-gradient(180deg,#e9e6e3,#c6a88f);border-radius:70px 70px 0 0}
.section-title{font-size:30px;line-height:36px;font-weight:400}
.new-title{left:89px;top:1195px;width:480px}
.bullets{list-style:none;font-size:12.6px;line-height:16px}
.bullets li{position:relative;padding-left:18px;margin-bottom:12px}
.bullets li::before{content:"";position:absolute;left:2px;top:4px;width:8px;height:8px;border-radius:50%;background:#111}
.new-list{left:89px;top:1280px;width:440px}

/* orange cta */
.cta-orange{left:0;top:1579px;width:1200px;height:171px;background:var(--orange)}
.cta-leaf{left:0;top:1545px;width:105px;height:205px;background:linear-gradient(200deg,rgba(14,140,62,.8),rgba(14,140,62,.25))}
.cta-hex{left:1118px;top:1585px;width:82px;height:160px;background:var(--orange-deep);opacity:.7;border-radius:18px 0 0 18px}
.cta-title{font-size:29px;line-height:36px}
.cta-one{left:91px;top:1627px;width:640px}
.btn{display:flex;align-items:center;justify-content:center;font-size:12.5px;font-weight:500;color:#fff;border-radius:4px}
.btn-green{left:917px;top:1650px;width:112px;height:29px;background:var(--green)}

/* professional */
.ring-green{left:151px;top:1861px;width:414px;height:414px;border:15px solid var(--green)}
.ring-green .fill{width:100%;height:100%;background:linear-gradient(160deg,#c9b29d 0%,#9dc0df 45%,#f1ece3 70%,#54796a 100%)}
.bee-decor{left:490px;top:1790px;width:115px;height:222px;background:linear-gradient(170deg,rgba(14,140,62,.35),rgba(242,173,47,.2));border-radius:40px}
.flower-decor{left:1055px;top:1797px;width:145px;height:458px;background:linear-gradient(180deg,#f6a01a,#f07b10 50%,#e9a63a);border-radius:80px 0 0 80px}
.pro-title{left:631px;top:1937px;width:440px}
.pro-list{left:631px;top:2019px;width:430px}

/* grey cta */
.cta-grey{left:0;top:2365px;width:1200px;height:171px;background:var(--grey-band)}
.cta-two{left:91px;top:2418px;width:640px}
.btn-orange{left:932px;top:2435px;width:112px;height:30px;background:var(--orange)}

/* contact */
.contact-box{left:90px;top:2686px;width:1019px;height:191px;background:var(--orange)}
.bouquet-photo{left:169px;top:2575px;width:344px;height:302px;background:radial-gradient(ellipse at 50% 35%,#d9549c 0%,#b35cc2 35%,#8fbf3f 65%,rgba(180,200,190,.6) 100%);border-radius:48% 48% 10% 10%}
.contact-line{left:538px;top:2754px;width:560px;font-size:23px;line-height:27px;color:#fff}
.contact-line a{color:var(--link);text-decoration:underline}

/* footer */
.site-footer{left:0;top:2862px;width:1200px;height:244px;background:var(--green-dark)}
.footer-brand{left:0;width:1200px;top:2943px;text-align:center;font-family:"Libre Baskerville",serif;font-size:30px;color:#fff}
.social{left:530px;top:3004px;display:flex;gap:9px}
.social span{width:28px;height:28px;border-radius:50%;background:rgba(255,255,255,.25)}
.footer-rule{left:181px;top:3067px;width:854px;height:1px;background:rgba(255,255,255,.35)}
.footer-small{top:3081px;font-size:10px;color:#fff}
.copy{left:185px}
.terms{left:820px}
.privacy{left:956px}
</style>
</head>
<body>

<header class="abs site-header">
  <div class="abs brand-name"><span class="brand-dot"></span>Lantern Petals</div>
  <div class="abs menu-toggle" aria-label="Menu"><span></span><span></span><span></span></div>
</header>

<section>
  <div class="abs hero-photo" role="img" aria-label="Flat lay of tulips, lavender, pink flowers, twine and shears on kraft paper over a wooden table"></div>
  <div class="abs hero-brand">LANTERN PETALS</div>
  <h1 class="abs hero-title serif" style="font-weight:700">Franchisees</h1>
</section>

<section>
  <div class="abs hex-decor" role="img" aria-label="Orange honeycomb decoration"></div>
  <div class="abs leaf-decor" role="img" aria-label="Green leaf stem decoration"></div>
  <div class="abs photo-ring ring-orange"><div class="fill" role="img" aria-label="Smiling florist holding a bouquet of purple, white and pink flowers"></div></div>
  <div class="abs intro-copy">
    <p>Lantern Petals brings the best of professional florists and supermarkets together for the benefit of consumers.&nbsp; It supports a national network of owner-operator franchisees with comprehensive services to enhance franchise profits.&nbsp; Lantern Petals works with some of the country’s largest and most progressive supermarkets to provide franchisee ownership and operation of their strategically important floral departments.</p>
    <p>Our franchisees are the cornerstone of our business.&nbsp; Many of them are already professional florists or florist employees who wish to expand their businesses without the significant costs of a traditional flower shop. Others are creative types or flower lovers who have made a career change in order to express their talents and make people happy.&nbsp; Still others are entrepreneurs in search of owning their own business.&nbsp; All are welcome if they meet Lantern Petals’ high standards of quality, service and ethical business practices.</p>
  </div>
</section>

<section>
  <div class="abs florist-band" role="img" aria-label="Florist in an apron at a flower shop counter with shelves of gifts behind him"></div>
  <div class="abs florist-photo-head" role="img" aria-label="Florist photo continuing above the band"></div>
  <h2 class="abs section-title serif new-title">Opportunity for New Florist Franchisees</h2>
  <ul class="abs bullets new-list">
    <li>No experience necessary, we set you up to operate and provide extensive support</li>
    <li>Professional training provided, and a path to floral design industry certification</li>
    <li>Low operating and supply costs which leverage supermarket economies</li>
    <li>Be an owner and your own boss while nurturing your creativity</li>
    <li>Attractive earnings potential; paid weekly</li>
    <li>Affordable franchise fees and low initial investment</li>
    <li>Opportunities to expand to different locations</li>
  </ul>
</section>

<section>
  <div class="abs cta-orange"></div>
  <div class="abs cta-leaf" role="img" aria-label="Green leaf stem decoration"></div>
  <div class="abs cta-hex" role="img" aria-label="Orange honeycomb decoration"></div>
  <h2 class="abs cta-title serif cta-one">Fill Out the Florist Inquiry Form and Let's Grow Beautiful Blooms Together!</h2>
  <a class="abs btn btn-green">Inquire Now</a>
</section>

<section>
  <div class="abs bee-decor" role="img" aria-label="Bee illustration with dotted flight path"></div>
  <div class="abs photo-ring ring-green"><div class="fill" role="img" aria-label="Smiling florist holding a bouquet of white peonies in a shop"></div></div>
  <div class="abs flower-decor" role="img" aria-label="Orange gerbera daisies"></div>
  <h2 class="abs section-title serif pro-title">Opportunity for Professional Floral Retailers</h2>
  <ul class="abs bullets pro-list">
    <li>Become a multi-site florist</li>
    <li>Add a high volume, high traffic location</li>
    <li>Enhance customer acquisition for specialty custom events</li>
    <li>Reduce product costs</li>
    <li>Leverage staffing across locations</li>
    <li>locations</li>
    <li>Leverage Lantern Petals best-in-class technology, support and marketing across</li>
  </ul>
</section>

<section>
  <div class="abs cta-grey"></div>
  <h2 class="abs cta-title serif cta-two">Unlock Your Floral Potential – Fill Out the Professional Florist Inquiry Form Today!</h2>
  <a class="abs btn btn-orange">Inquire Now</a>
</section>

<section>
  <div class="abs contact-box"></div>
  <div class="abs bouquet-photo" role="img" aria-label="Bouquet of lilies, roses and mixed flowers in a glass vase"></div>
  <p class="abs contact-line serif">For questions and further information, contact <a>info@lantern-petals.com</a></p>
</section>

<footer class="abs site-footer"></footer>
<div class="abs footer-brand">Lantern Petals</div>
<div class="abs social" aria-label="Social links"><span></span><span></span><span></span><span></span></div>
<div class="abs footer-rule"></div>
<div class="abs footer-small copy">© 2024 Lantern Petals, All rights reserved</div>
<div class="abs footer-small terms">Terms &amp; conditions</div>
<div class="abs footer-small privacy">Privacy policy</div>

</body>
</html>
```